Brenlow Estates Website and Logo Design

We need a new logo and website designed for 'Brenlow Estates Ltd', which is a well established Guernsey property holding company founded in 1934.

The company does not currently have a website. The new website should be similar in style and layout to https://www.quorvanhall.example/.

Target Market(s)

Industry, Media, Tenants

Industry/Entity Type

Property Management

Logo Text

BEL OR Brenlow Estates Ltd OR BE

Coding

Coded - Design and coding required

Number of Pages Required

4 page

Font styles to use
Other font styles liked:
• Helvetica

Requirements
Must have
• The logo laying over the picture (like https://www.quorvanhall.example/).
• Big pictures on homepage (like https://www.quorvanhall.example/)

```html
<!DOCTYPE html>
<html lang="en">
<head>
<meta charset="utf-8">
<title>Brenlow Estates Ltd</title>
<link rel="stylesheet" href="https://fonts.googleapis.com/css2?family=Marcellus+SC&family=Marcellus&family=Open+Sans:wght@400;600&family=Great+Vibes&display=swap">
<style>
:root{
  --blue:#0ba3ea;
  --blue-light:#4dbff1;
  --ink:#222;
  --text:#666;
  --band:#ececec;
  --white:#fff;
}
*{box-sizing:border-box;margin:0;padding:0}
html,body{width:1200px;height:3082px;overflow:hidden;background:var(--white)}
body{position:relative;font-family:"Open Sans",Arial,sans-serif;color:var(--text)}
.abs{position:absolute}

/* header */
.topline{left:0;top:0;width:1200px;height:5px;background:var(--blue)}
.brand{left:78px;top:18px;display:flex;align-items:center;gap:16px}
.brand-dot{flex:none;width:84px;height:84px;border:3px solid var(--blue);border-radius:50%}
.brand-name{font-family:"Marcellus SC",Georgia,serif;color:var(--blue);font-size:34px;line-height:1.05}
.head-contact{top:24px;text-align:center;color:var(--blue);font-size:18px;white-space:nowrap}
.head-contact svg{display:block;margin:0 auto 10px}
.head-divider{left:880px;top:22px;width:1px;height:80px;background:#ddd}
.nav{left:0;top:115px;width:1200px;height:52px;background:var(--blue);display:flex;justify-content:center}
.nav a{color:var(--white);text-decoration:none;font-size:16px;line-height:52px;width:180px;text-align:center}
.nav a.active{color:#06243a}

/* hero */
.hero{left:0;top:167px;width:1200px;height:510px;background:linear-gradient(100deg,#d8d2ec 0%,#e6d8ea 35%,#b9c3e4 60%,#8da3cf 80%,#b89a86 100%)}
.hero-copy{left:80px;top:300px}
.hero-tag{font-family:"Great Vibes",cursive;font-size:20px;color:#111;margin-top:30px}
.hero-title{font-family:"Marcellus",Georgia,serif;font-weight:400;font-size:56px;color:#111;letter-spacing:1px;line-height:1.1;margin-top:4px}
.hero-text{font-size:15px;color:#222;width:330px;line-height:1.5;margin-top:8px}

/* quote */
.quote{left:78px;top:662px;width:1044px;height:136px;background:var(--blue-light);box-shadow:0 2px 6px rgba(0,0,0,.15);padding:18px 12px}
.quote h2{font-family:"Marcellus SC",Georgia,serif;font-weight:400;color:#102a3a;font-size:26px;line-height:1}
.quote-row{display:flex;gap:12px;margin-top:20px}
.quote-row span{width:271px;height:42px;border:1px solid rgba(255,255,255,.8);color:var(--white);font-size:13px;padding:0 12px;line-height:40px}
.btn-white{background:var(--white);color:var(--blue);font-size:16px;text-align:center;width:141px;height:37px;line-height:37px;margin-left:auto;align-self:center}

.title{width:1200px;left:0;text-align:center;font-family:"Marcellus SC",Georgia,serif;font-weight:400;font-size:40px;color:#1d1d1d}
.title b{font-weight:400;color:var(--blue)}
.title.blue{color:var(--blue)}

.photo{border:1px solid #2c6c9c}
.about-text{left:590px;top:962px;width:525px;font-size:14.5px;line-height:1.68}
.btn-blue{background:var(--blue);color:var(--white);font-size:15px;text-align:center;line-height:45px}
.arrow{top:1285px}

/* testimonials */
.band{left:0;top:1446px;width:1200px;height:364px;background:var(--band)}
.band-title{left:110px;top:1575px;font-family:"Marcellus SC",Georgia,serif;font-weight:400;font-size:28px;color:#111}
.card{top:1500px;width:284px;height:208px;background:var(--white);padding:26px 22px 0 70px;font-size:15.5px;line-height:1.5;color:#333}
.card cite{display:block;margin-top:10px;font-family:"Marcellus SC",Georgia,serif;font-style:normal;color:var(--blue);font-size:15px}
.avatar{width:106px;height:106px;border-radius:50%;border:4px solid var(--white);background:linear-gradient(160deg,#6b4a3a,#c9a08d 55%,#c2272e)}
.dots{left:572px;top:1738px;display:flex;gap:6px}
.dots i{width:11px;height:11px;border-radius:50%;border:1.5px solid #333}
.dots i.on{background:#2c86b8;border-color:#2c86b8}

.lead{left:120px;top:1920px;width:960px;text-align:center;font-size:15px;line-height:1.7;color:#555}
.col{top:2296px;width:344px;text-align:center}
.col h3{font-family:"Marcellus",Georgia,serif;font-weight:400;font-size:21px;color:#111}
.col p{font-size:14.5px;line-height:1.6;margin:6px auto 0;width:320px;color:#555}
.col a{display:block;margin-top:12px;color:var(--blue);font-family:"Marcellus",Georgia,serif;font-size:16px;text-decoration:underline}

/* newsletter */
.news{left:0;top:2455px;width:1200px;height:136px;background:var(--blue)}
.news h2{position:absolute;left:78px;top:28px;font-family:"Marcellus SC",Georgia,serif;font-weight:400;font-size:27px;color:#0b1e2a}
.news p{position:absolute;left:78px;top:64px;width:380px;font-size:15px;color:var(--white);line-height:1.45}
.news-input{left:493px;top:47px;width:470px;height:46px;border:1px solid rgba(255,255,255,.85);color:var(--white);font-size:16px;padding:0 12px;line-height:44px}
.news-btn{left:975px;top:46px;width:146px;height:46px;background:var(--white);color:var(--blue);font-size:15px;text-align:center;line-height:46px}

/* contact */
.field{border:1px solid #bbb;font-size:13px;color:#888;padding:0 14px;line-height:44px;height:46px}
.info{left:622px;font-size:15.5px;color:#444;display:flex;gap:14px;line-height:1.5}
.info svg{flex:none;margin-top:3px}
.foot-brand{left:928px;top:2736px;display:flex;align-items:center;gap:10px}
.foot-brand .brand-dot{width:56px;height:56px;border-width:2px}
.foot-brand .brand-name{font-size:22px;line-height:1.05}
.foot-text{left:938px;top:2808px;width:190px;font-size:15px;line-height:1.6;color:#888}
.social{top:2958px;width:42px;height:42px;border-radius:50%;border:2px solid var(--blue)}
.social.fill{background:var(--blue)}
.footer{left:0;top:3030px;width:1200px;height:52px;background:var(--blue);color:var(--white);text-align:center;line-height:52px;font-size:15px}
</style>
</head>
<body>

<div class="abs topline"></div>
<div class="abs brand"><span class="brand-dot"></span><span class="brand-name">Brenlow Estates Ltd</span></div>

<div class="abs head-contact" style="left:700px;width:160px">
  <svg width="52" height="34" viewBox="0 0 52 34"><ellipse cx="20" cy="13" rx="18" ry="11" fill="#666"/><path d="M8 22l-3 9 10-6z" fill="#666"/><ellipse cx="34" cy="19" rx="14" ry="9" fill="#666"/></svg>
  123 456 7878
</div>
<div class="abs head-divider"></div>
<div class="abs head-contact" style="left:890px;width:260px">
  <svg width="50" height="34" viewBox="0 0 50 34"><rect x="2" y="2" width="46" height="30" fill="none" stroke="#555" stroke-width="3"/><path d="M2 2l23 18L48 2M2 32l17-15M48 32L31 17" fill="none" stroke="#555" stroke-width="3"/></svg>
  hello@brenlowestates.example
</div>

<nav class="abs nav">
  <a class="active">HOME</a><a>ABOUT US</a><a>PROJECTS</a><a>NEWS</a><a>CONTACT US</a>
</nav>

<div class="abs hero" role="img" aria-label="Coastal city skyline with high-rise towers beside a beach at dusk"></div>
<div class="abs hero-copy">
  <svg width="30" height="28" viewBox="0 0 30 28"><path d="M15 2L1 15h4v11h8v-8h4v8h8V15h4z" fill="#111"/></svg>
  <p class="hero-tag">How innovation , not regulation,can improve public health</p>
  <h1 class="hero-title">REAL HOMES</h1>
  <p class="hero-text">Lorem Ipsum is simply dummy text of the printing and typesetting.</p>
</div>

<section class="abs quote">
  <h2>Get a Professional Services,Get A Quote</h2>
  <div class="quote-row">
    <span>Name</span><span>E-Mail Id</span><span>Phone No.</span>
    <div class="btn-white">SUBMIT</div>
  </div>
</section>

<svg class="abs" style="left:584px;top:846px" width="32" height="28" viewBox="0 0 30 28"><path d="M15 2L1 15h4v11h8v-8h4v8h8V15h4z" fill="#ccc"/></svg>
<h2 class="abs title" style="top:868px">About <b>Us</b></h2>

<div class="abs photo" style="left:78px;top:928px;width:480px;height:287px;background:linear-gradient(180deg,#3f9ee0 0%,#7fc3ea 45%,#3aa6c5 70%,#cfd8de 100%)" role="img" aria-label="Palm trees and a modern villa terrace overlooking turquoise sea"></div>
<p class="abs about-text">Brenlow Estates Limited (BEL) is a family-owned Guernsey property holding company. It purchases properties that are considered to have potential for development either through refurbishment or by obtaining planning permission to change its classification from, for example, industrial premises to offices or retail outlets, or by the marriage value of buying an adjacent property to one already owned by BEL.</p>
<div class="abs btn-blue" style="left:590px;top:1133px;width:143px;height:45px">READ MORE</div>

<svg class="abs arrow" style="left:26px" width="18" height="56" viewBox="0 0 18 56"><path d="M16 2L3 28l13 26" fill="none" stroke="#aaa" stroke-width="2"/></svg>
<div class="abs" style="left:78px;top:1235px;width:252px;height:155px;background:linear-gradient(180deg,#6d8a55,#d9dcd8 50%,#3e5a32)" role="img" aria-label="White residential towers among green trees"></div>
<div class="abs" style="left:342px;top:1235px;width:254px;height:155px;background:linear-gradient(180deg,#2b68b8,#6fa3d8 45%,#8a7050 75%,#3c4a2e)" role="img" aria-label="Stone fort on rocky coastline under blue sky"></div>
<div class="abs" style="left:606px;top:1235px;width:254px;height:155px;background:linear-gradient(180deg,#5aa7e0,#e6e2d4 55%,#48b3b0 80%,#d9cfa8)" role="img" aria-label="Beach house with palm trees by the sea"></div>
<div class="abs" style="left:870px;top:1235px;width:252px;height:155px;background:linear-gradient(180deg,#7aa6d6,#dfe6ee 50%,#4f7fa6 85%)" role="img" aria-label="Modern waterfront apartment building"></div>
<svg class="abs arrow" style="left:1156px" width="18" height="56" viewBox="0 0 18 56"><path d="M2 2l13 26L2 54" fill="none" stroke="#aaa" stroke-width="2"/></svg>

<div class="abs band"></div>
<h2 class="abs band-title">Happy Customer</h2>
<div class="abs card" style="left:488px">"Lorem Ipsum is simply dummy text of the printing and typesetting industry. Lorem Ipsum has been summy text."<cite>- Client's Name</cite></div>
<div class="abs avatar" style="left:437px;top:1586px" role="img" aria-label="Customer portrait"></div>
<div class="abs card" style="left:838px">"Lorem Ipsum is simply dummy text of the printing and typesetting industry. Lorem Ipsum has been summy text."<cite>- Client's Name</cite></div>
<div class="abs avatar" style="left:787px;top:1586px" role="img" aria-label="Customer portrait"></div>
<div class="abs dots"><i class="on"></i><i></i><i></i><i></i></div>

<h2 class="abs title blue" style="top:1856px">Why Guernsey?</h2>
<p class="abs lead">The Bailiwick of Guernsey is a British Crown dependency in the English Channel. The benefit of establishing a company in Guernsey is the island's low tax jurisdiction since there are no capital taxes and no corporation taxes for many companies.</p>

<div class="abs photo" style="left:78px;top:2018px;width:344px;height:260px;background:linear-gradient(180deg,#f4f6f8 0%,#e6e8ea 35%,#7fa069 65%,#3f8a2a 100%)" role="img" aria-label="Traditional house with red roof on a green lawn"></div>
<div class="abs photo" style="left:428px;top:2018px;width:344px;height:260px;background:linear-gradient(180deg,#8aa6c8 0%,#b5c3d2 35%,#8a8f95 60%,#3f5d7a 100%)" role="img" aria-label="Harbour town with moored boats"></div>
<div class="abs photo" style="left:780px;top:2018px;width:344px;height:260px;background:linear-gradient(180deg,#3d94e0 0%,#9bd0ee 45%,#2fb3c7 70%,#c9b99a 100%)" role="img" aria-label="Resort pool lined with palm trees by the sea"></div>

<div class="abs col" style="left:78px"><h3>YESTERDAY</h3><p>BEL was founded in 1934 by Edmund Brenlow to manage both his own extensive...</p><a>READ MORE</a></div>
<div class="abs col" style="left:428px"><h3>TODAY</h3><p>The Brenlow family has steadily built on the foundations set out by the founder ...</p><a>READ MORE</a></div>
<div class="abs col" style="left:780px"><h3>TOMORROW</h3><p>In keeping with its past project development philosophy, its intrinsic...</p><a>READ MORE</a></div>

<section class="abs news">
  <h2>Sucribe Newsletter</h2>
  <p>Lorem Ipsum is simply dummy text of the printing and typesetting industry.</p>
  <div class="abs news-input">Email Id</div>
  <div class="abs news-btn">SUCRIBE NOW</div>
</section>

<h2 class="abs title blue" style="top:2638px">Contact Us</h2>
<div class="abs field" style="left:78px;top:2737px;width:190px">Name</div>
<div class="abs field" style="left:290px;top:2737px;width:203px">Contact No.</div>
<div class="abs field" style="left:78px;top:2790px;width:415px">E mail ID</div>
<div class="abs field" style="left:78px;top:2843px;width:415px;height:87px">Message...</div>
<div class="abs btn-blue" style="left:78px;top:2937px;width:144px;height:44px;line-height:44px">SUBMIT</div>

<div class="abs info" style="top:2728px"><svg width="14" height="20" viewBox="0 0 14 20"><path d="M7 1a6 6 0 0 0-6 6c0 5 6 12 6 12s6-7 6-12a6 6 0 0 0-6-6z" fill="#777"/><circle cx="7" cy="7" r="2.3" fill="#fff"/></svg><span>123,Lorem Ipsum,<br>Country,Zip Code.</span></div>
<div class="abs info" style="top:2792px"><svg width="16" height="16" viewBox="0 0 16 16"><path d="M3 1l3 3-2 2c1 2 3 4 5 5l2-2 3 3-2 3C7 15 1 9 1 3z" fill="#777"/></svg><span>123 456 7878</span></div>
<div class="abs info" style="top:2835px"><svg width="18" height="14" viewBox="0 0 18 14"><rect x="1" y="1" width="16" height="12" fill="none" stroke="#777" stroke-width="1.5"/><path d="M1 1l8 6 8-6" fill="none" stroke="#777" stroke-width="1.5"/></svg><span>office@brenlowestates.example</span></div>

<div class="abs foot-brand"><span class="brand-dot"></span><span class="brand-name">Brenlow Estates<br>Ltd</span></div>
<p class="abs foot-text">Lorem Ipsum is simply dummy text of the printing and typesetting.</p>
<span class="abs social fill" style="left:922px"></span>
<span class="abs social" style="left:975px"></span>
<span class="abs social" style="left:1028px"></span>
<span class="abs social" style="left:1081px"></span>

<footer class="abs footer"><strong>© Brenlow Estates Ltd.</strong> - 2016 All Right Reserved.</footer>

</body>
</html>
```